Mobile welding fabrication and repair, heavy equipment and semi repair

We need a business card design that will catch the eye but look prelesional at the same time. Were based out of Idaho and we do all welding fabrication jobs and repairs, we also build and install custom pipe fences for personal or larger scale fence jobs and can give free quotes. We can do semi truck and trailer repairs Mobily also.

Target Market(s)

Welding

Industry/Entity Type

welding and repair

Contact Information for Business Card

email (ravenforgeandmend@mailbay.net, phone number 208-417-3826, owner (Dalton Whitcomb), Pipe Fence, Semi Repair, Mobile welding and fabrication

Font styles to use
Sans Serif

Requirements
Must have
• My logo in black background on one side , and other side my logo in white back round with all the information listed on card details
Nice to have
• make it stand out from other business cards

```html
<!DOCTYPE html>
<html lang="en">
<head>
<meta charset="utf-8">
<title>Raven Forge and Mend – Business Card</title>
<link rel="stylesheet" href="https://fonts.googleapis.com/css2?family=Montserrat:wght@400;500;600;800&display=swap">
<style>
  :root {
    --stage: #2b2b2d;
    --blue-light: #1aa0dc;
    --blue-mid: #0f7fd0;
    --blue-deep: #0a4fb8;
    --ink: #222326;
    --paper: #ffffff;
    --rule: #555;
  }
  * { box-sizing: border-box; margin: 0; padding: 0; }
  html, body { width: 1200px; height: 1015px; overflow: hidden; }
  body {
    background: var(--stage);
    font-family: "Montserrat", sans-serif;
    position: relative;
  }
  .card {
    position: absolute;
    left: 250px;
    width: 700px;
    height: 400px;
    overflow: hidden;
    box-shadow: 0 14px 30px rgba(0,0,0,.55);
  }
  /* Back side */
  .card-back {
    top: 70px;
    background: linear-gradient(160deg, var(--blue-light) 0%, var(--blue-mid) 50%, var(--blue-deep) 100%);
  }
  .card-back .texture {
    position: absolute; inset: 0;
    background: linear-gradient(160deg, rgba(255,255,255,.05), rgba(0,0,0,.06));
  }
  .card-back .wordmark {
    position: absolute;
    right: 110px;
    bottom: 70px;
    color: var(--paper);
    font-weight: 800;
    font-size: 26px;
    letter-spacing: 3px;
  }
  /* Front side */
  .card-front {
    top: 530px;
    background: var(--paper);
  }
  .card-front .logo {
    position: absolute;
    left: 0; right: 0; top: 52px;
    text-align: center;
    color: var(--blue-mid);
    font-weight: 800;
    line-height: 1;
  }
  .logo .logo-main { display: block; font-size: 78px; letter-spacing: 4px; }
  .logo .logo-sub { display: block; font-size: 21px; letter-spacing: 3px; margin-top: 8px; }
  .contact {
    position: absolute;
    left: 0; right: 0; top: 190px;
    text-align: center;
    color: var(--ink);
  }
  .contact .person { color: var(--blue-deep); font-weight: 600; font-size: 25px; letter-spacing: 1px; }
  .contact .role { font-size: 15px; font-weight: 500; letter-spacing: 1px; margin-top: 2px; }
  .contact .divider { width: 90px; height: 1px; background: var(--rule); margin: 6px auto 8px; }
  .contact .line { font-size: 15px; line-height: 1.45; }
  .services {
    position: absolute;
    left: 0; right: 0; bottom: 0;
    height: 46px;
    background: linear-gradient(90deg, var(--blue-mid), var(--blue-light) 50%, var(--blue-mid));
    color: var(--paper);
    font-size: 15px;
    font-weight: 500;
    letter-spacing: .5px;
    display: flex; align-items: center; justify-content: center; gap: 10px;
  }
  .services .dot { width: 7px; height: 7px; border-radius: 50%; background: var(--paper); }
</style>
</head>
<body>
  <section class="card card-back" aria-label="Card back">
    <div class="texture" role="img" aria-label="Repeating brand name pattern on blue gradient"></div>
    <div class="wordmark">RAVEN</div>
  </section>

  <section class="card card-front" aria-label="Card front">
    <div class="logo">
      <span class="logo-main">RAVEN</span>
      <span class="logo-sub">FORGE AND MEND</span>
    </div>
    <div class="contact">
      <p class="person">DALTON WHITCOMB</p>
      <p class="role">OWNER</p>
      <div class="divider"></div>
      <p class="line">208-417-3826</p>
      <p class="line">ravenforgeandmend@mailbay.net</p>
    </div>
    <div class="services">
      <span>FABRICATION</span><span class="dot"></span>
      <span>MOBILE WELDING</span><span class="dot"></span>
      <span>SEMI REPAIR</span><span class="dot"></span>
      <span>PIPE FENCE</span>
    </div>
  </section>
</body>
</html>
```